BUSINESS CARD - HALLORAN FIELD SERVICES

I would like to create a business card for my fertilizer spreading business. I would like to incorporate my existing logo and also a description of the services offered. The business card will be given to farmers so must be kept simple but effective. It will also be left in stores so much also be eye catching in order to stand out from other cards.

Target Market(s)

FARMERS

Requirements
Must have
• FRONT OF CARD = EXISTING LOGO + "CUSTOMISED SPREADING" below the logo

REAR Of CARD = SERVICES OFFERED AND CONTACT DETAILS

- Bulk fertilizer including Lime, Gypsum, Manure & Compost
- Granular fertilizer including Single Super, Urea, MAP, & Custom Blends
- Modern equipment - Autosteer & Variable Rate Capable
- Friendly & Reliable Service
- Contact Gus: 0417 552 308
Nice to have
• utilize same color scheme as existing logo

```html
<!DOCTYPE html>
<html lang="en">
<head>
<meta charset="utf-8">
<title>Halloran Field Services – Business Card</title>
<link href="https://fonts.googleapis.com/css2?family=Arimo:wght@400;700&family=Open+Sans:wght@600;700&display=swap" rel="stylesheet">
<style>
  :root {
    --orange: #f7941e;
    --charcoal: #58585a;
    --text: #4a4a4c;
    --paper: #ffffff;
    --backdrop: #e4e5e6;
    --shadow: rgba(0, 0, 0, 0.45);
  }
  * { box-sizing: border-box; margin: 0; padding: 0; }
  html, body {
    width: 1200px;
    height: 900px;
    overflow: hidden;
    background: var(--backdrop);
  }
  .stage {
    position: relative;
    width: 1200px;
    height: 900px;
  }
  .card {
    position: absolute;
    top: 217px;
    width: 309px;
    height: 500px;
    box-shadow: 2px 2px 2px var(--shadow);
  }
  /* Front */
  .card--front {
    left: 279px;
    background: var(--orange);
    border-radius: 0 66px 0 66px;
    color: var(--paper);
    font-family: "Open Sans", sans-serif;
  }
  .front-mark {
    position: absolute;
    left: 0;
    right: 0;
    top: 168px;
    display: flex;
    flex-direction: column;
    align-items: center;
    gap: 14px;
  }
  .front-mark__dot {
    width: 56px;
    height: 56px;
    border-radius: 50%;
    background: var(--paper);
  }
  .front-mark__name {
    font-weight: 700;
    font-size: 17px;
    line-height: 1.25;
    text-align: center;
    letter-spacing: 0.5px;
    color: var(--paper);
  }
  .front-tagline {
    position: absolute;
    left: 0;
    right: 0;
    top: 431px;
    text-align: center;
    font-weight: 600;
    font-size: 16px;
    letter-spacing: 0.2px;
  }
  /* Back */
  .card--back {
    left: 617px;
    background: var(--paper);
    border-radius: 66px 0 66px 0;
    font-family: "Arimo", sans-serif;
    color: var(--text);
    text-align: center;
  }
  .back-mark {
    position: absolute;
    left: 0;
    right: 0;
    top: 56px;
    display: flex;
    flex-direction: column;
    align-items: center;
    gap: 12px;
  }
  .back-mark__dot {
    width: 90px;
    height: 90px;
    border-radius: 50%;
    background: var(--charcoal);
  }
  .back-mark__name {
    font-weight: 700;
    font-size: 22px;
    line-height: 25px;
    color: var(--charcoal);
  }
  .services {
    position: absolute;
    left: 0;
    right: 0;
    top: 255px;
    list-style: none;
    font-size: 14.5px;
    line-height: 17px;
  }
  .services li { margin-bottom: 5px; }
  .contact {
    position: absolute;
    left: 0;
    right: 0;
    top: 421px;
  }
  .contact__heading {
    display: flex;
    align-items: center;
    justify-content: center;
    gap: 8px;
    font-size: 20px;
    line-height: 22px;
  }
  .contact__heading::before,
  .contact__heading::after {
    content: "";
    width: 53px;
    height: 1px;
    background: var(--charcoal);
  }
  .contact__line {
    margin-top: 3px;
    font-size: 21px;
    line-height: 24px;
  }
  .contact__phone { color: var(--orange); }
</style>
</head>
<body>
<main class="stage">
  <section class="card card--front" aria-label="Card front">
    <div class="front-mark">
      <span class="front-mark__dot"></span>
      <p class="front-mark__name">HALLORAN FIELD<br>SERVICES</p>
    </div>
    <p class="front-tagline">CUSTOMISED SPREADING</p>
  </section>

  <section class="card card--back" aria-label="Card back">
    <div class="back-mark">
      <span class="back-mark__dot"></span>
      <p class="back-mark__name">HALLORAN FIELD<br>SERVICES</p>
    </div>
    <ul class="services">
      <li>Bulk fertilizer including Lime<br>Gypsum, Manure &amp; Compost</li>
      <li>Granular fertilizer including Single<br>Super, Urea, MAP, &amp; Custom Blends</li>
      <li>Modern equipment</li>
      <li>Autosteer &amp; Variable Rate Capable</li>
      <li>Friendly &amp; Reliable Service</li>
    </ul>
    <div class="contact">
      <p class="contact__heading">Contact</p>
      <p class="contact__line">Gus: <span class="contact__phone">0417 552 308</span></p>
    </div>
  </section>
</main>
</body>
</html>
```